Veltrane Group Business Card Design

The CEO is looking for a new trendy look for his business card.
You can stay with current branding or come up with something new/creative. It can be 3D, including Medical Office buildings. You can use our logo in a variety of colors. Please include name, title, company name, company website, email address, cell number

Target Market(s)

Real Estate Development and Construction

Industry/Entity Type

Health care real estate

Contact Information for Business Card

Rohesh Kamdar, CEO M-604.781.2249 E-roheshkamdar@veltrane.com Address:4180 Lindqvist Ave, Tampa, FL 33482 www.veltrane.com

Font styles to use
Other font styles liked:
• Be creative

Requirements
Must have
• Creative, trendy look
Nice to have
• Please go to our website to get a feel- www. veltrane.com
Should not have
• small fonts

```html
<!DOCTYPE html>
<html lang="en">
<head>
<meta charset="utf-8">
<title>Veltrane Group Business Card</title>
<link href="https://fonts.googleapis.com/css2?family=Poppins:wght@400;600;700&display=swap" rel="stylesheet">
<style>
  :root {
    --brand-red: #b31f2b;
    --brand-red-light: #c5262f;
    --brand-navy: #1c2c4c;
    --ink: #2a2a2a;
    --card-white: #ffffff;
    --rule: #c8c8c8;
    --backdrop: #9b9b9b;
  }
  * { margin: 0; padding: 0; box-sizing: border-box; }
  html, body {
    width: 1093px; height: 1200px; overflow: hidden;
    background: var(--backdrop);
    font-family: "Poppins", sans-serif;
  }
  .canvas { position: relative; width: 1093px; height: 1200px; }

  .card {
    position: absolute; left: 265px; width: 578px; height: 357px;
    border-radius: 24px; overflow: hidden;
  }
  .card-front { top: 226px; background: var(--card-white); }
  .card-back { top: 621px; background: var(--brand-red); }

  .wordmark {
    position: absolute; color: var(--brand-red); font-weight: 700;
    line-height: 1; text-align: right;
  }
  .card-front .wordmark { left: 30px; top: 128px; width: 236px; font-size: 46px; letter-spacing: -1px; }
  .wordmark .wordmark-sub { display: block; font-size: 26px; letter-spacing: 0; margin-top: 2px; }

  .divider {
    position: absolute; left: 288px; top: 74px; width: 1px; height: 209px;
    background: var(--rule);
  }

  .details { position: absolute; left: 311px; top: 92px; }
  .person-name { color: var(--brand-red); font-weight: 700; font-size: 24px; line-height: 1.1; }
  .person-title { color: var(--brand-navy); font-size: 16px; line-height: 1.1; }
  .contact-list { list-style: none; margin-top: 14px; }
  .contact-list li {
    display: flex; align-items: center; gap: 7px;
    color: var(--ink); font-size: 16px; line-height: 21px;
  }
  .contact-list svg { width: 15px; height: 15px; flex: none; fill: var(--brand-red); }
  .address { margin-top: 16px; color: var(--ink); font-size: 16px; line-height: 21px; }

  .edge-band { position: absolute; left: 0; bottom: 0; width: 578px; height: 12px; }

  .card-back .wordmark {
    left: 0; right: 0; top: 132px; width: auto; text-align: center;
    color: var(--brand-red-light); font-size: 64px; letter-spacing: -1px;
  }
  .card-back .wordmark .wordmark-sub { font-size: 34px; }
</style>
</head>
<body>
<main class="canvas">

  <section class="card card-front" aria-label="Business card front">
    <div class="wordmark">Veltrane<span class="wordmark-sub">Group</span></div>
    <div class="divider"></div>
    <div class="details">
      <h1 class="person-name">Rohesh Kamdar</h1>
      <p class="person-title">CEO</p>
      <ul class="contact-list">
        <li>
          <svg viewBox="0 0 24 24" aria-hidden="true"><path d="M6.6 10.8a15.1 15.1 0 0 0 6.6 6.6l2.2-2.2a1 1 0 0 1 1-.25 11.4 11.4 0 0 0 3.6.57 1 1 0 0 1 1 1V20a1 1 0 0 1-1 1A17 17 0 0 1 3 4a1 1 0 0 1 1-1h3.5a1 1 0 0 1 1 1c0 1.25.2 2.45.57 3.57a1 1 0 0 1-.25 1z"/></svg>
          604.781.2249
        </li>
        <li>
          <svg viewBox="0 0 24 24" aria-hidden="true"><path d="M2 5h20v14H2z M2 5l10 8 10-8" stroke="#fff" stroke-width="1.5"/></svg>
          roheshkamdar@veltrane.com
        </li>
        <li>
          <svg viewBox="0 0 24 24" aria-hidden="true"><circle cx="12" cy="12" r="10"/><path d="M2 12h20M12 2c3 3 3 17 0 20M12 2c-3 3-3 17 0 20M4 7h16M4 17h16" stroke="#fff" stroke-width="1.2" fill="none"/></svg>
          www.veltrane.com
        </li>
      </ul>
      <p class="address">4180 Lindqvist Ave, Tampa<br>FL 33482</p>
    </div>
    <svg class="edge-band" viewBox="0 0 578 12" preserveAspectRatio="none" aria-hidden="true">
      <polygon points="0,0 506,0 502,12 0,12" fill="var(--brand-red)"/>
      <polygon points="510,0 578,0 578,12 506,12" fill="var(--brand-navy)"/>
    </svg>
  </section>

  <section class="card card-back" aria-label="Business card back">
    <div class="wordmark">Veltrane<span class="wordmark-sub">Group</span></div>
  </section>

</main>
</body>
</html>
```